Business Card

Just need business logo with phone number on it. 0487 312 654
And the following on the bottom of the card.

"Your local plumbing experts".
and emblems for zelpa card, cheque and cash

```html
<!DOCTYPE html>
<html lang="en">
<head>
<meta charset="utf-8">
<title>Eastbrook Plumbing &amp; Drainage – Business Card</title>
<link href="https://fonts.googleapis.com/css2?family=Roboto:wght@400;700&display=swap" rel="stylesheet">
<style>
  :root{
    --backdrop:#e5e5e5;
    --card:#f9f9f9;
    --brand-red:#dd2a1f;
    --brand-blue:#0a7bc4;
    --wave-blue:#0c7cc6;
    --white:#ffffff;
  }
  *{margin:0;padding:0;box-sizing:border-box}
  html,body{width:1200px;height:608px;overflow:hidden;background:var(--backdrop);font-family:'Roboto',Arial,sans-serif}
  .stage{position:relative;width:1200px;height:608px}
  .card{position:absolute;top:205px;width:327px;height:197px;background:var(--card);overflow:hidden}
  .card--front{left:237px}
  .card--back{left:635px}

  .brand{display:flex;align-items:center;gap:8px;color:var(--brand-red);font-weight:700;line-height:1.05}
  .brand__dot{border-radius:50%;background:var(--brand-blue);flex:none}
  .brand__name small{display:block;text-transform:uppercase}

  .card--front .brand{position:absolute;left:50%;top:50%;transform:translate(-50%,-50%)}
  .card--front .brand__dot{width:18px;height:18px}
  .card--front .brand__name{font-size:27px;letter-spacing:.3px}
  .card--front .brand__name small{font-size:11.5px;letter-spacing:1.1px;margin-top:2px}

  .card--back .brand{position:absolute;left:20px;top:27px}
  .card--back .brand__dot{width:15px;height:15px}
  .card--back .brand__name{font-size:22px;letter-spacing:.3px}
  .card--back .brand__name small{font-size:9.5px;letter-spacing:1px;margin-top:2px}

  .contact{position:absolute;left:22px;top:89px}
  .contact__name{color:var(--brand-red);font-weight:700;font-size:14px;margin-bottom:6px}
  .contact__row{display:flex;align-items:center;gap:5px;color:var(--brand-blue);font-size:8.5px;line-height:11px}
  .contact__row--phone{font-weight:700;font-size:11px;line-height:14px}
  .contact__row svg{width:7px;height:7px;fill:var(--brand-red);flex:none}

  .waves{position:absolute;left:0;bottom:0;width:327px;height:197px}
  .tagline{position:absolute;right:34px;top:149px;color:var(--white);font-size:9.5px;line-height:12px;text-align:center}

  .payments{position:absolute;right:38px;top:178px;display:flex;gap:4px}
  .payments__badge{width:17px;height:11px;border-radius:2px;background:var(--white)}
  .payments__badge--card{background:var(--white)}
  .payments__badge--cheque{background:#dbe9f5}
  .payments__badge--cash{background:#cfe6d2}
</style>
</head>
<body>
<main class="stage">
  <section class="card card--front" aria-label="Card front">
    <div class="brand">
      <span class="brand__dot"></span>
      <span class="brand__name">Eastbrook<small>Plumbing &amp; Drainage</small></span>
    </div>
  </section>

  <section class="card card--back" aria-label="Card back">
    <svg class="waves" viewBox="0 0 327 197" aria-hidden="true">
      <path fill="var(--wave-blue)" d="M0,172 C60,194 110,198 160,178 C210,155 240,135 290,134 C310,134 320,136 327,137 L327,197 L0,197Z"/>
      <path fill="var(--brand-red)" d="M0,148 C50,175 100,190 150,178 C200,160 230,118 280,118 C305,118 320,122 327,125 L327,131 C310,127 295,125 280,126 C235,129 205,168 150,184 C100,196 50,180 0,158Z"/>
    </svg>

    <div class="brand">
      <span class="brand__dot"></span>
      <span class="brand__name">Eastbrook<small>Plumbing &amp; Drainage</small></span>
    </div>

    <div class="contact">
      <p class="contact__name">Sam Carter</p>
      <p class="contact__row contact__row--phone">
        <svg viewBox="0 0 10 10"><path d="M1 3C1 2 2 1 3 1L4 3 3 4C4 5.5 4.5 6 6 7L7 6 9 7C9 8 8 9 7 9 3.5 9 1 6.5 1 3Z"/></svg>
        0487 312 654
      </p>
      <p class="contact__row">
        <svg viewBox="0 0 10 10"><path d="M0 2H10V8H0ZM1 3V3.4L5 6 9 3.4V3L5 5.4Z"/></svg>
        sam@eastbrookplumbing.com
      </p>
      <p class="contact__row">
        <svg viewBox="0 0 10 10"><circle cx="5" cy="5" r="4.5"/><path d="M.5 5H9.5M5 .5V9.5" stroke="#fff" stroke-width=".8"/></svg>
        www.eastbrookplumbing.com
      </p>
    </div>

    <p class="tagline">Your Local<br>Plumbing Experts</p>

    <div class="payments" aria-label="Accepted payments">
      <span class="payments__badge payments__badge--card" role="img" aria-label="zelpa card accepted"></span>
      <span class="payments__badge payments__badge--cheque" role="img" aria-label="Cheque accepted"></span>
      <span class="payments__badge payments__badge--cash" role="img" aria-label="Cash accepted"></span>
    </div>
  </section>
</main>
</body>
</html>
```